Recruitment Agency in Texas, needs a stand out header letter

Our colours are red and grey and can be found on our website
just my logo will be sufficient and address...

Target Market(s)

Engineering Manufacturing

Colors
0094D4
00A9DD
6FCCEA
C7EBF8
E9F6FB
EB3D1F
EC4F4E
F09395
F8D3D4
FCEDEE

Requirements
Must have
• use colors red and grey
Should not have
• Please use same colors and font as my logo. My website is keltrayrecruitment.com

```html
<!DOCTYPE html>
<html lang="en">
<head>
<meta charset="utf-8">
<title>Keltray Recruitment Letterhead</title>
<link rel="stylesheet" href="https://fonts.googleapis.com/css2?family=Open+Sans:wght@400;600&family=Roboto:wght@400;500&display=swap">
<style>
  :root {
    --bg: #dcdcdc;
    --paper: #f8f8f8;
    --ink: #4a4a4a;
    --grey: #5f5f62;
    --red: #d2202a;
    --sig-fill: #e6e6e6;
  }
  * { margin: 0; padding: 0; box-sizing: border-box; }
  html, body {
    width: 1153px;
    height: 1200px;
    overflow: hidden;
    background: var(--bg);
  }
  .letterhead {
    position: absolute;
    left: 146px;
    top: 0;
    width: 860px;
    height: 1200px;
    background: var(--paper);
    font-family: "Open Sans", Arial, sans-serif;
    color: var(--ink);
  }
  .brand {
    position: absolute;
    top: 96px;
    left: 0;
    width: 100%;
    text-align: center;
    font-family: "Open Sans", Arial, sans-serif;
    font-weight: 600;
    font-size: 48px;
    letter-spacing: -0.5px;
    color: var(--red);
    line-height: 1;
  }
  .letter-body {
    position: absolute;
    left: 77px;
    width: 704px;
    top: 266px;
    font-size: 15.6px;
    line-height: 23px;
  }
  .letter-body p {
    text-align: justify;
    margin-bottom: 23px;
  }
  .letter-body .salutation { margin-bottom: 23px; }
  .signature {
    position: absolute;
    left: 78px;
    top: 877px;
    width: 103px;
    height: 94px;
    background: var(--sig-fill);
  }
  .contact-bar {
    position: absolute;
    left: 77px;
    top: 1090px;
    width: 704px;
    font-family: "Roboto", Arial, sans-serif;
    font-size: 17.5px;
    line-height: 24px;
    color: var(--ink);
  }
  .contact-col { position: absolute; top: 0; white-space: nowrap; }
  .contact-col.phone { left: 0; }
  .contact-col.office { left: 191px; }
  .contact-col.online { left: 448px; }
  .label { color: var(--red); font-weight: 500; }
</style>
</head>
<body>
  <main class="letterhead">
    <header class="brand">KeltrayRecruitment</header>

    <section class="letter-body">
      <p class="salutation">Dear customer,</p>
      <p>Lorem ipsum dolor sit amet, consectetur adipisicing elit, sed do eiusmod tempor incididunt ut labore et dolore magna aliqua. Ut enim ad minim veniam, quis nostrud exercitation ullamco laboris nisi ut aliquip ex ea commodo consequat. Duis aute irure dolor in reprehenderit in voluptate velit esse cillum dolore eu fugiat nulla pariatur. Excepteur sint occaecat cupidatat non proident, sunt in culpa qui officia deserunt mollit anim id est laborum.</p>
      <p>Lorem ipsum dolor sit amet, consectetur adipisicing elit, sed do eiusmod tempor incididunt ut labore et dolore magna aliqua. Ut enim ad minim veniam, quis nostrud exercitation ullamco laboris nisi ut aliquip ex ea commodo consequat. Duis aute irure dolor in reprehenderit in voluptate velit esse cillum dolore eu fugiat nulla pariatur. Excepteur sint occaecat cupidatat non proident, sunt in culpa qui officia deserunt mollit anim id est laborum.</p>
      <p>Lorem ipsum dolor sit amet, consectetur adipisicing elit, sed do eiusmod tempor incididunt ut labore et dolore magna aliqua. Ut enim ad minim veniam, quis nostrud exercitation ullamco laboris nisi ut aliquip ex ea commodo consequat. Duis aute irure dolor in reprehenderit in voluptate velit esse cillum dolore eu fugiat nulla pariatur. Excepteur sint occaecat cupidatat non proident, sunt in culpa qui officia deserunt mollit anim id est laborum.</p>
      <p>Lorem ipsum dolor sit amet, consectetur adipisicing elit, sed do eiusmod tempor incididunt ut labore et dolore magna aliqua. Ut enim ad minim veniam, quis nostrud exercitation ullamco laboris nisi ut aliquip ex ea commodo consequat. Duis aute irure dolor in reprehenderit.</p>
      <p class="closing">Yours Sincerely,</p>
    </section>

    <div class="signature" role="img" aria-label="Handwritten signature of the sender"></div>

    <footer class="contact-bar">
      <div class="contact-col phone">
        <div><span class="label">T:</span> (+1) 832-555-0147</div>
        <div><span class="label">Fax:</span> 832-555-0148</div>
      </div>
      <div class="contact-col office">
        <div>Houston Office</div>
        <div>48 Meridian Plaza Houston</div>
      </div>
      <div class="contact-col online">
        <div><span class="label">E:</span> info@keltrayrecruitment.com</div>
        <div><span class="label">W:</span> www.keltrayrecruitment.com</div>
      </div>
    </footer>
  </main>
</body>
</html>
```